Redesign of business card for Cedar Ridge Mechanical

We are looking for a new design for our business cards for Cedar Ridge Mechanical. We are a plumbing & HVAC construction company, operating on the West Coast of Canada and USA. Logo attached.
Industry/Entity Type
Construction - Plumbing & HVAC
Contact Information for Business Card
Name, address, phone numbers, email, website address
Look and feel
Each slider illustrates characteristics of the customer's brand and the style your logo design should communicate.

```html
<!DOCTYPE html>
<html lang="en">
<head>
<meta charset="utf-8">
<title>Cedar Ridge Mechanical – Business Card</title>
<link href="https://fonts.googleapis.com/css2?family=Poppins:wght@300;400;600;700&display=swap" rel="stylesheet">
<style>
  :root {
    --bg: #222222;
    --card: #1f1f21;
    --ink: #ffffff;
    --ink-soft: #e6e6e6;
    --emboss: #2c2c2f;
  }
  * { margin: 0; padding: 0; box-sizing: border-box; }
  html, body { width: 1200px; height: 780px; overflow: hidden; background: var(--bg); }
  body { font-family: "Poppins", sans-serif; color: var(--ink); position: relative; }

  .card {
    position: absolute;
    width: 540px;
    height: 309px;
    background: var(--card);
    border-radius: 6px;
    overflow: hidden;
    box-shadow: 0 18px 40px rgba(0,0,0,0.45);
  }
  .card--front { left: 40px; top: 236px; }
  .card--back  { left: 620px; top: 236px; }

  /* Front */
  .front-curve { position: absolute; inset: 0; }
  .front-brand {
    position: absolute; left: 30px; top: 70px;
    width: 170px;
    display: flex; align-items: center; gap: 10px;
    font-size: 15px; line-height: 1.25; font-weight: 600; letter-spacing: 0.5px;
  }
  .brand-square { width: 14px; height: 14px; background: var(--ink); flex: none; }

  .holder { position: absolute; right: 44px; top: 44px; text-align: right; }
  .holder-name { font-size: 30px; line-height: 1.1; font-weight: 300; white-space: nowrap; }
  .holder-name strong { font-weight: 700; }
  .holder-title { font-size: 14px; font-weight: 400; margin-top: 4px; color: var(--ink-soft); }
  .accent-bar {
    position: absolute; right: 0; top: 44px;
    width: 22px; height: 62px; background: var(--ink);
  }

  .contact {
    position: absolute; right: 30px; bottom: 28px;
    list-style: none; text-align: right;
    font-size: 13px; line-height: 1.55; font-weight: 300;
  }
  .contact li { display: flex; justify-content: flex-end; align-items: center; gap: 10px; }
  .contact .icon { width: 13px; height: 13px; flex: none; }
  .contact .icon-gap { width: 13px; flex: none; }
  .contact .address { margin-bottom: 6px; }

  /* Back */
  .back-brand {
    position: absolute; inset: 0;
    display: flex; align-items: center; justify-content: center; gap: 14px;
    font-size: 24px; font-weight: 700; letter-spacing: 1px;
    color: var(--emboss);
  }
  .back-brand .brand-square { width: 22px; height: 22px; background: var(--emboss); }
</style>
</head>
<body>

<section class="card card--front" aria-label="Business card front">
  <svg class="front-curve" viewBox="0 0 540 309" preserveAspectRatio="none" aria-hidden="true">
    <defs>
      <linearGradient id="curveFade" x1="0" y1="0" x2="1" y2="1">
        <stop offset="0" stop-color="#2a2a2c"/>
        <stop offset="1" stop-color="#1f1f21"/>
      </linearGradient>
    </defs>
    <path d="M0 90 C 70 80, 150 140, 200 309 L 0 309 Z" fill="url(#curveFade)"/>
  </svg>

  <div class="front-brand"><span class="brand-square"></span><span>Cedar Ridge<br>Mechanical</span></div>

  <span class="accent-bar"></span>
  <div class="holder">
    <p class="holder-name"><strong>Marta</strong> Kovarova</p>
    <p class="holder-title">Founder &amp; CEO</p>
  </div>

  <ul class="contact">
    <li>1840 Harbor Ln. Suite 310<span class="icon-gap"></span></li>
    <li class="address">Portland, OR 97205<span class="icon-gap"></span></li>
    <li>(503) 555-0147
      <svg class="icon" viewBox="0 0 24 24" aria-hidden="true"><path fill="#fff" d="M6.6 10.8a15.1 15.1 0 0 0 6.6 6.6l2.2-2.2c.3-.3.7-.4 1-.2 1.1.4 2.3.6 3.6.6.6 0 1 .4 1 1V20c0 .6-.4 1-1 1A17 17 0 0 1 3 4c0-.6.4-1 1-1h3.5c.6 0 1 .4 1 1 0 1.3.2 2.5.6 3.6.1.3 0 .7-.2 1z"/></svg>
    </li>
    <li>info@cedarridgemech.com
      <svg class="icon" viewBox="0 0 24 24" aria-hidden="true"><rect x="2" y="5" width="20" height="14" rx="2" fill="#fff"/><path d="M3 6l9 7 9-7" fill="none" stroke="#1f1f21" stroke-width="2"/></svg>
    </li>
    <li>www.cedarridgemech.com
      <svg class="icon" viewBox="0 0 24 24" aria-hidden="true"><circle cx="12" cy="12" r="10" fill="#fff"/><path d="M2 12h20M12 2c3 3 3 17 0 20M12 2c-3 3-3 17 0 20" fill="none" stroke="#1f1f21" stroke-width="1.5"/></svg>
    </li>
  </ul>
</section>

<section class="card card--back" aria-label="Business card back">
  <div class="back-brand"><span class="brand-square"></span>Cedar Ridge Mechanical</div>
</section>

</body>
</html>
```